Flyer Design for an ornamental (Aquarium) food product called Prawn Joy Bramble

To design a product flyer for an ornamental (aquarium) food which is primarily made from the leaf of a Mulberry Tree. The flyer is a front and back however the back will be very simple, focus of the design is the first page of the PowerPoint.

• I have made a template in PowerPoint to base the design off of but please your creativity and design.

• Goals: Simple but eloquent

Target Market(s)

Home Aquarium Industry

Industry/Entity Type

Pet

Colors

Designer to choose colors to be used in the design.

Requirements
Must have
• • In the PowerPoint I have used a photo of a real shrimp over heart but I would like the design to use a created graphic of a shrimp (please look up “crystal red shrimp” – and there are even graphic versions of ornamental shrimp to use as reference when image searched). Please do NOT use image/graphic of a shrimp that is used for human consumption.
• The name of the product is "Prawn Joy Bramble", on the design please use a graphic of a heart to represent the word "Love" - similar to the PowerPoint.
Nice to have
• • Colour: Open to creative design in you can convince me, but I do like white background, red for the heart, dark green relates to the mulberry leaves.
• • Font – You do not need to use the font in the PowerPoint, use whatever font you think looks best
Should not have
• Please do NOT use image/graphic of a shrimp that is used for human consumption.
• As described in the must haves: (please look up “crystal red shrimp” – and there are even graphic versions of ornamental shrimp to use as reference when image searched)."

```html
<!DOCTYPE html>
<html lang="en">
<head>
<meta charset="utf-8">
<title>Prawn Joy Bramble – Flyer Front and Back</title>
<link rel="stylesheet" href="https://fonts.googleapis.com/css2?family=Josefin+Sans:wght@600&family=Yanone+Kaffeesatz:wght@400&family=EB+Garamond:wght@400;500&display=swap">
<style>
  :root {
    --stage: #3b3b3b;
    --paper: #f6f0df;
    --paper-edge: #eee5cd;
    --art-red: #e0402a;
    --art-red-soft: rgba(224, 64, 42, 0);
    --name-purple: #3a1f6e;
    --leaf-green: rgba(79, 138, 58, .75);
    --berry-dark: rgba(70, 40, 85, .8);
    --ink: #2a2622;
    --accent-red: #c0262a;
  }
  * { box-sizing: border-box; margin: 0; padding: 0; }
  html, body { width: 1200px; height: 1024px; overflow: hidden; }
  body { background: var(--stage); position: relative; font-family: "EB Garamond", Georgia, serif; color: var(--ink); }

  .flyer-page {
    position: absolute; top: 133px; width: 540px; height: 757px;
    background: radial-gradient(ellipse at 50% 45%, var(--paper) 60%, var(--paper-edge) 100%);
    box-shadow: 0 6px 18px rgba(0, 0, 0, .45);
  }
  .flyer-front { left: 40px; }
  .flyer-back { left: 620px; }

  .sprig-art {
    position: absolute; top: 0; width: 130px; height: 140px;
    background: linear-gradient(160deg, var(--leaf-green), var(--berry-dark) 55%, rgba(246, 240, 223, 0) 95%);
    opacity: .55;
  }
  .sprig-left { left: 0; }
  .sprig-right { right: 0; transform: scaleX(-1); }

  .shrimp-art {
    position: absolute; left: 130px; width: 280px; height: 350px;
    background: radial-gradient(ellipse at 50% 45%, var(--art-red) 0 45%, var(--art-red-soft) 72%);
    opacity: .8;
  }
  .flyer-front .shrimp-art { top: 125px; }
  .flyer-back .shrimp-art { top: 134px; }

  .product-name {
    position: absolute; top: 502px; left: 0; width: 100%; text-align: center;
    font-family: "Josefin Sans", sans-serif; font-weight: 600; font-size: 46px;
    color: var(--name-purple); letter-spacing: .5px;
  }
  .subtitle-leaf {
    position: absolute; top: 563px; left: 0; width: 100%; text-align: center;
    font-family: "Yanone Kaffeesatz", sans-serif; font-size: 31px; color: var(--ink);
  }
  .subtitle-use {
    position: absolute; top: 600px; left: 0; width: 100%; text-align: center;
    font-family: "Yanone Kaffeesatz", sans-serif; font-size: 20px; color: var(--ink);
  }
  .source-lead { position: absolute; top: 644px; left: 28px; font-size: 15.5px; }
  .benefit-list { list-style: none; position: absolute; top: 674px; left: 26px; width: 500px; height: 50px; font-size: 13px; }
  .benefit-list li { position: absolute; padding-left: 16px; white-space: nowrap; }
  .benefit-list li::before {
    content: ""; position: absolute; left: 0; top: 4px; width: 8px; height: 8px;
    border: 2px solid var(--accent-red); border-radius: 50%;
  }
  .net-weight { position: absolute; top: 722px; right: 24px; font-size: 11px; }

  .back-copy { position: absolute; left: 22px; width: 496px; font-size: 10.5px; line-height: 1.25; text-align: justify; }
  .back-copy b { font-weight: 500; font-size: 14px; }
  .copy-intro { top: 527px; }
  .copy-feeding { top: 583px; }
  .copy-storage { top: 643px; }
  .produced-by { position: absolute; top: 694px; left: 22px; font-size: 11px; color: var(--accent-red); }
  .contact-line { position: absolute; top: 712px; left: 22px; width: 500px; display: flex; align-items: flex-start; gap: 6px; font-size: 10.5px; line-height: 1.2; }
  .contact-line svg { width: 10px; height: 10px; flex: none; margin-top: 2px; }
  .contact-item { display: flex; gap: 5px; margin-right: 4px; }
</style>
</head>
<body>

<section class="flyer-page flyer-front">
  <div class="sprig-art sprig-left" role="img" aria-label="Watercolour mulberry sprig with leaves and dark berries"></div>
  <div class="sprig-art sprig-right" role="img" aria-label="Watercolour mulberry sprig with leaves and dark berries"></div>
  <div class="shrimp-art" role="img" aria-label="Illustration of two red ornamental shrimp"></div>
  <h1 class="product-name">Prawn Joy Bramble</h1>
  <p class="subtitle-leaf">Mulberry Leaf</p>
  <p class="subtitle-use">Based Dietary Supplement for all Ornamental Shrimp</p>
  <p class="source-lead">Mulberry Leaves are a Natural Source of -</p>
  <ul class="benefit-list">
    <li style="left:0;top:0">Vitamin A, B, C, and K</li>
    <li style="left:178px;top:0">Dietary Fibre</li>
    <li style="left:328px;top:0">Best of all shrimp LOVE it!!!</li>
    <li style="left:0;top:24px">Calcium, Iron, and Potassium</li>
    <li style="left:178px;top:24px">Beneficial phytonutrients</li>
  </ul>
  <p class="net-weight">Net Weight: Four x 3g tubes</p>
</section>

<section class="flyer-page flyer-back">
  <div class="sprig-art sprig-left" role="img" aria-label="Watercolour mulberry sprig with leaves and dark berries"></div>
  <div class="sprig-art sprig-right" role="img" aria-label="Watercolour mulberry sprig with leaves and dark berries"></div>
  <div class="shrimp-art" role="img" aria-label="Illustration of two red ornamental shrimp"></div>
  <p class="back-copy copy-intro"><b>Prawn Joy Bramble</b> is designed to be used as part of a varied diet for your shrimp. It comes in a convenient applicator to easily control and provide the exact amount of food you want to feed.</p>
  <p class="back-copy copy-feeding"><b>Feeding Instructions:</b> Use as part of a varied diet for your shrimp. Feed once a day, the amount will vary with the number of shrimp present. Avoid over feeding and remove any uneaten food to avoid water quality issues.</p>
  <p class="back-copy copy-storage"><b>Storage:</b> Keep frozen for long term storage. Remove one applicator at time. After an applicator is removed from the freezer and thawed discard any remaining food after one month. Store the applicator in the refrigerator between feedings.</p>
  <p class="produced-by">Produced in Australia by:</p>
  <div class="contact-line">
    <span class="contact-item">
      <svg viewBox="0 0 10 10"><rect x="0.5" y="2" width="9" height="6.5" fill="none" stroke="#2a2622"/><path d="M0.5 2 L5 6 L9.5 2" fill="none" stroke="#2a2622"/></svg>
      info@prawnjoybramble.com
    </span>
    <span class="contact-item">
      <svg viewBox="0 0 10 10"><circle cx="5" cy="5" r="4.5" fill="none" stroke="#2a2622"/><ellipse cx="5" cy="5" rx="2" ry="4.5" fill="none" stroke="#2a2622"/><line x1="0.5" y1="5" x2="9.5" y2="5" stroke="#2a2622"/></svg>
      www.prawnjoybramble.com
    </span>
    <span class="contact-item">
      <svg viewBox="0 0 10 10"><path d="M5 0.5 L9.5 5 H8 V9.5 H6 V6.5 H4 V9.5 H2 V5 H0.5 Z" fill="#2a2622"/></svg>
      <span>Prawn Joy Bramble, PO Box 2240<br>Ferntree Hill, VIC 3999</span>
    </span>
  </div>
</section>

</body>
</html>
```